Create a book cover for brimvale QTR

We are looking for a designer to design a cover for a log book in two versions. The two versions only have a slight difference in page count and text, other than that, it is one design.

The main color is blue. No black, no white except book title and other text. The cover must closely relate to the interior pages provided in the attachment. The style should be simple and modern, no old school graphics and fonts. Apply color psychology in the design. Please be creative and you are allowed to use download templates and graphic elements, but you must provide commercial licenses.

Here are the basic information of the book:
1. Book title: MOTOR UPKEEP TRACKING JOURNAL
2. Book size: 6x9 inches
3. Page count: 61 (version 1) and 73 (version 2)
4. Platform: brimvale qtr

Requirement for version 1:
1. Front cover: book title
2. Spine: no book title and author name
3. Back cover: text on the top and pen name logo on the bottom middle
4. Back cover text:
• Your essential tool for tracking vehicle health and maintenance
• Dedicated sections for maintenance schedules and repair history
• Track up to 30 maintenance schedules and repair history
• Easy-to-use tables and clear layouts
• Perfect for all car owners, from enthusiasts to everyday drivers

We hope it helps you keep your vehicle in excellent condition. Please take a moment to leave a positive review on Brimvale and share your experience if you find it helpful. Thank you!

Requirement for version 2:
1. Front cover: book title ,text "COLOR PAGES"
4. Back cover text:
• Track up to 36 maintenance schedules and repair history

Export:
1. Cover design in PDF and editable file format.
2. Sources/Commercial licenses for everything you did not create by yourself including fonts.

```html
<!DOCTYPE html>
<html lang="en">
<head>
<meta charset="utf-8">
<title>Motor Upkeep Tracking Journal – Cover</title>
<link rel="stylesheet" href="https://fonts.googleapis.com/css2?family=Roboto+Condensed:wght@900&family=Montserrat:wght@500;600&display=swap">
<style>
  :root {
    --sky: #00d8fe;
    --backdrop: #00c8ec;
    --ink: #1a1a1a;
    --navy: #1c2434;
    --steel-light: #b9b9b5;
    --steel-dark: #6b6b68;
  }
  * { margin: 0; padding: 0; box-sizing: border-box; }
  html, body {
    width: 1200px; height: 1200px; overflow: hidden;
    background: var(--backdrop);
  }
  .cover {
    position: absolute; left: 128px; top: 248px;
    width: 943px; height: 704px;
    background: var(--sky);
    color: var(--ink);
  }
  .title-line {
    position: absolute;
    font-family: "Roboto Condensed", "Arial Narrow", sans-serif;
    font-weight: 900;
    line-height: 1;
    text-transform: uppercase;
    white-space: nowrap;
  }
  /* back cover title, centred on x = 237 inside the cover */
  .title--back .title-line { left: 237px; transform: translateX(-50%); }
  .title--back .l1 { top: 26px;  font-size: 78px; }
  .title--back .l2 { top: 98px;  font-size: 43px; }
  .title--back .l3 { top: 136px; font-size: 70px; }
  .title--back .l4 { top: 206px; font-size: 78px; }

  /* front cover title, left aligned, kept clear of the wrench */
  .title--front .title-line { left: 492px; }
  .title--front .l1 { top: 186px; font-size: 101px; }
  .title--front .l2 { top: 282px; font-size: 55px; }
  .title--front .l3 { top: 336px; font-size: 76px; }
  .title--front .l4 { top: 420px; font-size: 86px; }

  .blurb {
    position: absolute; left: 24px; top: 283px; width: 440px;
    font-family: "Montserrat", Arial, sans-serif;
    font-weight: 500; font-size: 11.5px;
  }
  .features { list-style: none; }
  .features li { line-height: 26.7px; white-space: nowrap; }
  .features li::before { content: "• "; }
  .thanks { margin-top: 14px; line-height: 16px; white-space: nowrap; }

  .pen-name {
    position: absolute;
    display: flex; align-items: center; gap: 8px;
    transform: translate(-50%, -50%);
    font-family: "Montserrat", Arial, sans-serif;
    font-weight: 600; font-size: 15px; letter-spacing: 1px;
    color: var(--ink);
    white-space: nowrap;
  }
  .pen-name__dot { width: 40px; height: 40px; border-radius: 50%; background: var(--navy); }
  .pen-name--back { left: 238px; top: 567px; }
  .pen-name--front { left: 710px; top: 612px; }

  .wrench-art {
    position: absolute; left: 858px; top: 61px;
    width: 58px; height: 526px;
    border-radius: 29px;
    background: linear-gradient(90deg, var(--steel-dark), var(--steel-light) 50%, var(--steel-dark));
  }
</style>
</head>
<body>
  <main class="cover">
    <section class="back-cover">
      <h2 class="title title--back">
        <span class="title-line l1">Motor</span>
        <span class="title-line l2">Upkeep</span>
        <span class="title-line l3">Tracking</span>
        <span class="title-line l4">Journal</span>
      </h2>
      <div class="blurb">
        <ul class="features">
          <li>Your essential tool for tracking vehicle health and maintenance</li>
          <li>Dedicated sections for maintenance schedules and repair history</li>
          <li>Track up to 30 maintenance schedules and repair history</li>
          <li>Easy-to-use tables and clear layouts</li>
          <li>Perfect for all car owners, from enthusiasts to everyday drivers</li>
        </ul>
        <p class="thanks">We hope it helps you keep your vehicle in excellent condition.<br>Please take a moment to leave a positive review on Brimvale and<br>share your experience if you find it helpful. Thank you!</p>
      </div>
      <div class="pen-name pen-name--back"><span class="pen-name__dot"></span>TOVAN HELLER</div>
    </section>

    <section class="front-cover">
      <h1 class="title title--front">
        <span class="title-line l1">Motor</span>
        <span class="title-line l2">Upkeep</span>
        <span class="title-line l3">Tracking</span>
        <span class="title-line l4">Journal</span>
      </h1>
      <div class="wrench-art" role="img" aria-label="Photograph of a steel combination wrench standing upright"></div>
      <div class="pen-name pen-name--front"><span class="pen-name__dot"></span>TOVAN HELLER</div>
    </section>
  </main>
</body>
</html>
```